GlassHaven Artbook for Okanagan Region, British Columbia

Creating an art book: GlassHaven, for the Okanagan Wine Region in British Columbia, Canada. Would like smart, modern, clean and linear...cool, sexy urban, not ugly boring suburban... I need a cover that appeals to the wino in all of us! Title: GlassHaven -Marla Dovicki
Updates
Thank you all kindly for your efforts. I have added some files so that you can get a sense of my aesthetic...it's never easy trying to figure it out, is it? I will hopefully have dimensions of book soon...cheers, Marla
would anyone please design a giant wine bottle with the wine label that looks like a label but says glasshaven...just curious to see if it works as a design or not...thank you.
Target Market(s)
Designing this wine art book of quotes to wineries in Okanagan BC. Buyer is wine lover and tourist ready to spend his vacation bucks on this wonderful book!
Look and feel

```html
<!DOCTYPE html>
<html lang="en">
<head>
<meta charset="utf-8">
<title>GlassHaven – Cover Variations</title>
<link rel="stylesheet" href="https://fonts.googleapis.com/css2?family=Source+Sans+3:ital,wght@0,600;1,300&display=swap">
<style>
  :root {
    --page: #ffffff;
    --wine: #9e2017;
    --scarlet: #ee2b26;
    --ink: #000000;
    --slate: #7a7c80;
    --band: #bcbec0;
    --light: #ffffff;
    --accent-bright: #e9282a;
  }
  html, body {
    margin: 0;
    padding: 0;
    width: 1200px;
    height: 1200px;
    overflow: hidden;
    background: var(--page);
  }
  .sheet {
    position: relative;
    width: 1200px;
    height: 1200px;
    font-family: "Source Sans 3", "Myriad Pro", sans-serif;
  }
  .cover {
    position: absolute;
    width: 472px;
    height: 472px;
    overflow: hidden;
    --accent: var(--accent-bright);
  }
  .cover--wine    { left: 116px; top: 110px; background: var(--wine); --accent: var(--wine); }
  .cover--scarlet { left: 621px; top: 110px; background: var(--scarlet); }
  .cover--ink     { left: 116px; top: 618px; background: var(--ink); }
  .cover--slate   { left: 621px; top: 618px; background: var(--slate); }

  .bottle-neck {
    position: absolute;
    left: 82px;
    top: 55px;
    width: 42px;
    height: 195px;
    background: linear-gradient(to bottom, rgba(255,255,255,0.55), rgba(255,255,255,0.9));
  }
  .bottle-body {
    position: absolute;
    left: 103px;
    top: 250px;
    width: 21px;
    height: 222px;
    background: var(--light);
  }
  .title-band {
    position: absolute;
    left: 0;
    top: 250px;
    width: 416px;
    height: 81px;
    background: var(--band);
  }
  .title {
    position: absolute;
    right: 16px;
    top: 50%;
    transform: translateY(-54%);
    margin: 0;
    font-weight: 600;
    font-size: 52px;
    letter-spacing: -1.5px;
    line-height: 1;
    color: var(--light);
  }
  .title .initial { color: var(--accent); }
  .author {
    position: absolute;
    right: 57px;
    top: 342px;
    margin: 0;
    font-weight: 300;
    font-style: italic;
    font-size: 21px;
    letter-spacing: -0.3px;
    color: var(--light);
  }
</style>
</head>
<body>
<main class="sheet">
  <section class="cover cover--wine">
    <div class="bottle-neck" role="img" aria-label="White wine bottle neck and shoulder silhouette"></div>
    <div class="bottle-body"></div>
    <div class="title-band"><h1 class="title"><span class="initial">g</span>lass<span class="initial">h</span>aven</h1></div>
    <p class="author">author name</p>
  </section>
  <section class="cover cover--scarlet">
    <div class="bottle-neck" role="img" aria-label="White wine bottle neck and shoulder silhouette"></div>
    <div class="bottle-body"></div>
    <div class="title-band"><h2 class="title"><span class="initial">g</span>lass<span class="initial">h</span>aven</h2></div>
    <p class="author">author name</p>
  </section>
  <section class="cover cover--ink">
    <div class="bottle-neck" role="img" aria-label="White wine bottle neck and shoulder silhouette"></div>
    <div class="bottle-body"></div>
    <div class="title-band"><h2 class="title"><span class="initial">g</span>lass<span class="initial">h</span>aven</h2></div>
    <p class="author">author name</p>
  </section>
  <section class="cover cover--slate">
    <div class="bottle-neck" role="img" aria-label="White wine bottle neck and shoulder silhouette"></div>
    <div class="bottle-body"></div>
    <div class="title-band"><h2 class="title"><span class="initial">g</span>lass<span class="initial">h</span>aven</h2></div>
    <p class="author">author name</p>
  </section>
</main>
</body>
</html>
```